I have a logo and need to design the business card and stationery.
Updates

The uploaded logo image named as GREYMARSH CONTRACTS which is to be replaced to GREYMARSH CONTRACTS. Kindly add below details and submit the designs- Company name- Greymarsh Engineering Contracts LLP Name & Post- Kelvan Joshi (Designated Partner) Address- Block No.317, Wing C, Tulvo Trade Court, Manek Pural Road, Ruparel Industrial Estate, Goregaon(E), Mumbai - 400 063 Contact- +91 97415 60382 Email- kelvanjoshi@mailbrook.example Website- www.greymarshcontracts.example Contact for Letterhead- +91-22-28754193

Hi Tovin Rahul, We are liking your Design #28860835. We have suggested some changes which are mentioned in feedback. Kindly revert with it asap to finalize this design.

Colors

Designer to choose colors to be used in the design.

```html
<!DOCTYPE html>
<html lang="en">
<head>
<meta charset="utf-8">
<title>Greymarsh Contracts – Business Card</title>
<link href="https://fonts.googleapis.com/css2?family=Arimo:wght@400;700&display=swap" rel="stylesheet">
<style>
  :root {
    --stage: #1c1c1c;
    --card-front: #ffffff;
    --card-back: #2c2c2c;
    --ink-dark: #1f1f1f;
    --ink-light: #f2f2f2;
    --ink-soft: #d6d6d6;
    --emboss: #383838;
  }
  * { box-sizing: border-box; margin: 0; padding: 0; }
  html, body {
    width: 1200px; height: 1015px; overflow: hidden;
    background: var(--stage);
    font-family: "Arimo", Arial, sans-serif;
  }
  .stage {
    width: 1200px; height: 1015px;
    display: flex; flex-direction: column;
    align-items: center; justify-content: center; gap: 48px;
  }
  .card {
    width: 760px; height: 434px;
    border-radius: 2px;
    position: relative;
    box-shadow: 0 10px 30px rgba(0,0,0,.5);
  }
  .card--front {
    background: var(--card-front);
    display: flex; align-items: center; justify-content: center;
  }
  .brand {
    display: flex; align-items: center; gap: 22px;
    color: var(--ink-dark);
  }
  .brand__square {
    width: 70px; height: 70px;
    border: 9px solid var(--ink-dark);
  }
  .brand__name {
    font-weight: 700; font-size: 34px; line-height: 1.15;
    letter-spacing: 1px;
  }
  .brand__name span { display: block; }
  .card--back {
    background: var(--card-back);
    color: var(--ink-light);
  }
  .contact {
    position: absolute; left: 62px; top: 66px;
    width: 360px;
  }
  .contact__name {
    font-weight: 700; font-size: 27px; letter-spacing: .5px;
  }
  .contact__role {
    font-size: 15px; color: var(--ink-soft); margin-top: 3px; letter-spacing: .3px;
  }
  .contact__list { list-style: none; margin-top: 28px; }
  .contact__list li {
    display: flex; align-items: center; gap: 9px;
    font-size: 17px; line-height: 26px; white-space: nowrap;
  }
  .contact__list svg { width: 16px; height: 16px; flex: none; }
  .contact__address {
    margin-top: 28px; font-size: 16px; line-height: 22px; font-style: normal;
  }
  .card__mark {
    position: absolute; right: 70px; top: 92px;
    width: 250px; height: 250px;
    border: 2px solid var(--emboss);
  }
</style>
</head>
<body>
<main class="stage">
  <section class="card card--front" aria-label="Card front">
    <div class="brand">
      <div class="brand__square" aria-hidden="true"></div>
      <p class="brand__name"><span>GREYMARSH</span><span>CONTRACTS</span></p>
    </div>
  </section>

  <section class="card card--back" aria-label="Card back">
    <div class="contact">
      <h1 class="contact__name">KELVAN JOSHI</h1>
      <p class="contact__role">DESIGNATED PARTNER</p>
      <ul class="contact__list">
        <li>
          <svg viewBox="0 0 24 24" fill="none" stroke="currentColor" stroke-width="2.2" stroke-linecap="round"><path d="M5 3h4l2 5-2.5 1.5a11 11 0 0 0 6 6L16 13l5 2v4a2 2 0 0 1-2 2A17 17 0 0 1 3 5a2 2 0 0 1 2-2z"/></svg>
          +91 97415 60382
        </li>
        <li>
          <svg viewBox="0 0 24 24" fill="none" stroke="currentColor" stroke-width="2.2"><rect x="2" y="5" width="20" height="14"/><path d="M2 5l10 8 10-8"/></svg>
          kelvanjoshi@mailbrook.example
        </li>
        <li>
          <svg viewBox="0 0 24 24" fill="none" stroke="currentColor" stroke-width="2"><circle cx="12" cy="12" r="10"/><path d="M2 12h20M12 2c3 3 3 17 0 20M12 2c-3 3-3 17 0 20"/></svg>
          www.greymarshcontracts.example
        </li>
      </ul>
      <address class="contact__address">Block No.317, Wing C, Tulvo Trade Court,<br>Manek Pural Road, Ruparel Industrial Estate,<br>Goregaon(E), Mumbai - 400 063</address>
    </div>
    <div class="card__mark" aria-hidden="true"></div>
  </section>
</main>
</body>
</html>
```